Simple, High-Class Web Design Wanted - Motivational Speakers Site

1. Full Brief/Request & Specs outlined on following video -
http://clipvault-demo.com/watch/rTkWmaPzQb

2. Use colours, images as you feel suits objective (we are happy to pay up to US$30 for any good images but must have licence/permission).

3. Layout probably similar to existing site - www.podiumtalentgroup.com.au / http://podiumtalentgroup.com.au/contact.php

4. Must Be Able to Coded for MOBILE-FRIENDLINESS & WordPress friendly Ideal.

5. This is the first, small job of many we/graphic design jobs. If suits, winning designer may be offered all future work direct.

Thanks & look forward to your design. Glen.

Target Market(s)

corporates - high end

Number of Pages Required

2 page

Font styles to use
Sans Serif

Requirements
Must have
• Classy professional look
Nice to have
• all in Video in brief
Should not have
• too many images / new images I haven't approved

```html
<!DOCTYPE html>
<html lang="en">
<head>
<meta charset="utf-8">
<title>Speaker Name – Guest &amp; Keynote Speaker</title>
<link href="https://fonts.googleapis.com/css2?family=Open+Sans:wght@400;600;700&family=Oswald:wght@400;500&display=swap" rel="stylesheet">
<style>
  :root{
    --hero-dark:#0d3f4a;
    --hero-green:#1f9a5a;
    --hero-blue:#1a6fb5;
    --brand-blue:#1e88d6;
    --title-blue:#1f7cc4;
    --text:#555;
    --grey-bg:#e6e6e6;
    --footer:#1c8bd8;
    --footer-dark:#0f4f8c;
    --white:#fff;
  }
  *{margin:0;padding:0;box-sizing:border-box}
  html,body{width:694px;height:1200px;overflow:hidden;background:#fff}
  body{font-family:"Open Sans",Arial,sans-serif;color:var(--text);position:relative}
  .abs{position:absolute}

  /* hero */
  .hero{left:0;top:0;width:694px;height:434px;
    background:linear-gradient(115deg,var(--hero-dark) 0%,#125a4f 30%,var(--hero-green) 55%,var(--hero-blue) 100%)}
  .topbar{left:0;top:0;width:694px;height:72px;background:rgba(0,20,30,.35)}
  .brand{left:42px;top:18px;font-family:"Oswald",sans-serif;font-weight:500;font-size:30px;color:var(--white);letter-spacing:.5px}
  .contact{top:24px;display:flex;align-items:center;gap:8px;color:var(--white);font-size:19px;font-family:"Oswald",sans-serif}
  .contact.phone{left:272px}
  .contact.mail{left:436px;padding-left:18px;border-left:1px solid rgba(255,255,255,.5)}
  .hero-copy{left:42px;top:168px;width:400px;color:var(--white);white-space:nowrap}
  .hero-copy .line{display:block;line-height:32px}
  .hero-copy .lead{font-size:22px;font-weight:400}
  .hero-copy .caps{font-family:"Oswald",sans-serif;font-weight:500;font-size:23px}
  .btn-hero{left:42px;top:318px;width:156px;height:34px;background:var(--white);color:var(--title-blue);
    font-family:"Oswald",sans-serif;font-size:18px;display:flex;align-items:center;justify-content:center}
  .hero-photo{left:446px;top:50px;width:224px;height:384px;
    background:linear-gradient(180deg,#3a4250 0%,#1e2430 60%,#15191f 100%);border-radius:90px 90px 0 0}

  /* welcome */
  .welcome-title{left:42px;top:468px;font-size:20px;font-weight:600;color:var(--title-blue)}
  .rule{height:2px;background:var(--brand-blue)}
  .welcome-rule{left:42px;top:500px;width:46px}
  .welcome-text{left:42px;top:512px;width:282px;font-size:9.5px;line-height:1.55}
  .btn-small{background:var(--brand-blue);color:var(--white);font-size:11px;font-weight:700;
    display:flex;align-items:center;justify-content:center}
  .btn-enquiry{left:42px;top:646px;width:108px;height:28px}
  .video-main{left:347px;top:476px;width:304px;height:176px;
    background:linear-gradient(135deg,#c9ced3,#9aa3ab 60%,#6d767e)}
  .play{position:absolute;left:50%;top:50%;transform:translate(-50%,-50%)}

  /* videos area */
  .grey{left:0;top:700px;width:694px;height:375px;background:var(--grey-bg)}
  .intro{left:92px;top:735px;width:510px;text-align:center;font-size:9.5px;line-height:1.55}
  .section-title{left:0;top:820px;width:694px;text-align:center;font-size:20px;font-weight:600;color:var(--title-blue)}
  .section-rule{left:323px;top:852px;width:48px}
  .card{top:873px;width:174px}
  .card .thumb{position:relative;width:174px;height:96px;border:4px solid var(--white)}
  .card h3{margin-top:12px;text-align:center;font-size:13px;font-weight:600;color:var(--title-blue)}
  .card p{margin-top:6px;text-align:center;font-size:9px;line-height:1.5}
  .t1{background:linear-gradient(135deg,#8a96a8,#3c4a63 70%,#5b4a44)}
  .t2{background:linear-gradient(135deg,#dfe4ea,#9aa6b4 60%,#2a3140)}
  .t3{background:linear-gradient(135deg,#eef2f5,#b9c3cc 55%,#2b313a)}

  /* footer */
  .footer{left:0;top:1075px;width:694px;height:102px;background:var(--footer)}
  .foot-col{top:1092px;color:var(--white)}
  .foot-col h4{font-size:12px;font-weight:600;margin-bottom:12px}
  .mail-field{display:flex;width:190px;height:26px}
  .mail-field span{flex:1;background:#1576bf;font-size:9px;color:#cde4f6;padding:7px 8px}
  .mail-field i{width:26px;background:#0f63a6;display:flex;align-items:center;justify-content:center}
  .foot-phone{display:flex;align-items:center;gap:8px;font-family:"Oswald",sans-serif;font-size:22px}
  .foot-mail{display:flex;align-items:center;gap:8px;font-size:11px}
  .bottom{left:0;top:1177px;width:694px;height:23px;background:var(--footer-dark);color:var(--white);
    font-size:9px;display:flex;align-items:center;justify-content:center}
</style>
</head>
<body>

<!-- hero -->
<div class="abs hero"></div>
<div class="abs hero-photo" role="img" aria-label="Portrait of the speaker in a dark suit, arms folded"></div>
<div class="abs topbar"></div>
<div class="abs brand">SPEAKER NAME</div>
<div class="abs contact phone">
  <svg width="20" height="20" viewBox="0 0 24 24"><path fill="#fff" d="M6.6 10.8a15.1 15.1 0 0 0 6.6 6.6l2.2-2.2c.3-.3.7-.4 1-.2 1.1.4 2.3.6 3.6.6.6 0 1 .4 1 1V20c0 .6-.4 1-1 1C10.6 21 3 13.4 3 4c0-.6.4-1 1-1h3.5c.6 0 1 .4 1 1 0 1.2.2 2.4.6 3.6.1.3 0 .7-.2 1z"/></svg>
  123 456 7890
</div>
<div class="abs contact mail">
  <svg width="20" height="16" viewBox="0 0 24 18"><rect x="1" y="1" width="22" height="16" fill="none" stroke="#fff" stroke-width="2"/><path d="M1 1l11 9 11-9" fill="none" stroke="#fff" stroke-width="2"/></svg>
  info@speakername.com.au
</div>
<h1 class="abs hero-copy">
  <span class="line lead">Are you looking for a Guest or</span>
  <span class="line lead">Keynote Speaker - <span class="caps">INSPIRING,</span></span>
  <span class="line caps">ENTERTAINING, INDUSTRY EXPERT ETC,</span>
  <span class="line caps">FOR A CONFERENCE OR SPECIAL EVENT?</span>
</h1>
<div class="abs btn-hero">CONTACT US NOW!</div>

<!-- welcome -->
<h2 class="abs welcome-title">Welcome to Speaker Name</h2>
<div class="abs rule welcome-rule"></div>
<p class="abs welcome-text">Lorem Ipsum is simply dummy text of the printing and typesetting industry. Lorem Ipsum has been the industry's standard dummy text ever since the 1500s, when an unknown printer took a galley of type and scrambled it to make a type specimen book. It has survived not only five centuries, but also the leap into electronic typesetting, remaining essentially unchanged. It was popularised in the 1960s with the release of Letraset sheets containing Lorem Ipsum passages.</p>
<div class="abs btn-small btn-enquiry">ENQUIRY NOW</div>
<div class="abs video-main" role="img" aria-label="Video still of the speaker talking to camera">
  <svg class="play" width="44" height="44" viewBox="0 0 44 44"><circle cx="22" cy="22" r="21" fill="#d22"/><path d="M17 13l14 9-14 9z" fill="#fff"/></svg>
</div>

<!-- latest videos -->
<div class="abs grey"></div>
<p class="abs intro">Lorem Ipsum is simply dummy text of the printing and typesetting industry. Lorem Ipsum has been the industry's standard dummy text ever since the 1500s, when an unknown printer took a galley of type and scrambled it to make a type specimen book. It has survived not only five centuries, but also the leap into electronic typesetting, remaining essentially unchanged. It was popularised in the 1960s with the release of Letraset sheets containing Lorem Ipsum passages.</p>
<h2 class="abs section-title">Our Latest Videos</h2>
<div class="abs rule section-rule"></div>

<div class="abs card" style="left:42px">
  <div class="thumb t1" role="img" aria-label="Speaker presenting on stage">
    <svg class="play" width="26" height="26" viewBox="0 0 44 44"><circle cx="22" cy="22" r="21" fill="#d22"/><path d="M17 13l14 9-14 9z" fill="#fff"/></svg>
  </div>
  <h3>Video Title</h3>
  <p>Lorem Ipsum is simply dummy text of the printing and typesetting industry. Lorem Ipsum has been the industry.</p>
</div>
<div class="abs card" style="left:260px">
  <div class="thumb t2" role="img" aria-label="Speaker addressing a conference audience">
    <svg class="play" width="26" height="26" viewBox="0 0 44 44"><circle cx="22" cy="22" r="21" fill="#d22"/><path d="M17 13l14 9-14 9z" fill="#fff"/></svg>
  </div>
  <h3>Video Title</h3>
  <p>Lorem Ipsum is simply dummy text of the printing and typesetting industry. Lorem Ipsum has been the industry.</p>
</div>
<div class="abs card" style="left:478px">
  <div class="thumb t3" role="img" aria-label="Business speaker in a bright office">
    <svg class="play" width="26" height="26" viewBox="0 0 44 44"><circle cx="22" cy="22" r="21" fill="#d22"/><path d="M17 13l14 9-14 9z" fill="#fff"/></svg>
  </div>
  <h3>Video Title</h3>
  <p>Lorem Ipsum is simply dummy text of the printing and typesetting industry. Lorem Ipsum has been the industry.</p>
</div>

<!-- footer -->
<div class="abs footer"></div>
<div class="abs foot-col" style="left:42px">
  <h4>Mailing list</h4>
  <div class="mail-field"><span>Enter your Email id</span><i><svg width="10" height="12" viewBox="0 0 10 12"><path d="M2 1l6 5-6 5" fill="none" stroke="#fff" stroke-width="2"/></svg></i></div>
</div>
<div class="abs foot-col" style="left:258px">
  <h4>Quick Contact No.</h4>
  <div class="foot-phone">
    <svg width="18" height="18" viewBox="0 0 24 24"><path fill="#fff" d="M6.6 10.8a15.1 15.1 0 0 0 6.6 6.6l2.2-2.2c.3-.3.7-.4 1-.2 1.1.4 2.3.6 3.6.6.6 0 1 .4 1 1V20c0 .6-.4 1-1 1C10.6 21 3 13.4 3 4c0-.6.4-1 1-1h3.5c.6 0 1 .4 1 1 0 1.2.2 2.4.6 3.6.1.3 0 .7-.2 1z"/></svg>
    123 456 7890
  </div>
</div>
<div class="abs foot-col" style="left:470px">
  <h4>Get In Touch Email</h4>
  <div class="foot-mail">
    <svg width="16" height="12" viewBox="0 0 24 18"><rect x="1" y="1" width="22" height="16" fill="none" stroke="#fff" stroke-width="2"/><path d="M1 1l11 9 11-9" fill="none" stroke="#fff" stroke-width="2"/></svg>
    info@speakername.com.au
  </div>
</div>
<div class="abs bottom">© <b>&nbsp;SPEAKER NAME&nbsp;</b> - 2015. All Rights Reserved.</div>

</body>
</html>
```